Investment company needing business card

We are wanting a business card which looks sharp and easy on the eye. We are thinking of having a business card with the logo embossed on it, to really make it stand out. We will only have a small amount of information of the business card, person's name, position, email address and phone number

Contact Information for Business Card

Danielle Frost
Executive Assistant
+64 21 473 5162
danielf@harwickpartners.co.nz

Requirements
Must have
• Embossed logo
Should not have
• Not to be busy

```html
<!DOCTYPE html>
<html lang="en">
<head>
<meta charset="utf-8">
<title>Harwick Partners – Business Card</title>
<link href="https://fonts.googleapis.com/css2?family=Open+Sans:wght@400;700&display=swap" rel="stylesheet">
<style>
  :root {
    --bg: #2a2a2b;
    --card: #ffffff;
    --green: #1fb36e;
    --grey: #5f5f61;
    --text: #555557;
  }
  * { margin: 0; padding: 0; box-sizing: border-box; }
  html, body { width: 1200px; height: 900px; overflow: hidden; }
  body {
    background: var(--bg);
    font-family: "Open Sans", Arial, sans-serif;
    position: relative;
  }
  .card {
    position: absolute;
    left: 290px;
    width: 620px;
    height: 354px;
    background: var(--card);
    border-radius: 18px;
    overflow: hidden;
  }
  .card--front { top: 70px; }
  .card--back { top: 476px; }

  .side-band {
    position: absolute; left: 0; top: 0; bottom: 0;
    width: 44px; background: var(--grey);
  }
  .side-stripe {
    position: absolute; left: 44px; top: 0; bottom: 0;
    width: 12px; background: var(--green);
  }

  .brand {
    position: absolute;
    display: flex; align-items: center; gap: 14px;
  }
  .brand-mark {
    width: 44px; height: 44px; background: var(--green); border-radius: 4px;
  }
  .brand-name {
    font-weight: 700; color: var(--green);
    font-size: 30px; letter-spacing: 1px; text-transform: uppercase;
    line-height: 1;
  }
  .card--front .brand { left: 84px; top: 54px; }
  .card--back .brand {
    left: 50%; top: 50%; transform: translate(-50%, -50%);
  }
  .card--back .brand-mark { width: 58px; height: 58px; }
  .card--back .brand-name { font-size: 36px; }

  .contact { position: absolute; left: 178px; top: 176px; }
  .person-name {
    font-weight: 700; color: var(--green); font-size: 20px;
    text-transform: uppercase; line-height: 1.1;
  }
  .person-role { color: var(--text); font-size: 17px; margin-bottom: 16px; }
  .contact-list { list-style: none; }
  .contact-item {
    display: flex; align-items: center; gap: 10px;
    color: var(--text); font-size: 16px; line-height: 25px;
  }
  .contact-icon {
    width: 17px; height: 17px; background: var(--green);
    border-radius: 3px; display: flex; align-items: center; justify-content: center;
  }
  .contact-icon svg { width: 11px; height: 11px; }
</style>
</head>
<body>
  <section class="card card--front">
    <div class="side-band"></div>
    <div class="side-stripe"></div>
    <div class="brand">
      <span class="brand-mark"></span>
      <span class="brand-name">Harwick Partners</span>
    </div>
    <div class="contact">
      <p class="person-name">Danielle Frost</p>
      <p class="person-role">Executive Assistant</p>
      <ul class="contact-list">
        <li class="contact-item">
          <span class="contact-icon"><svg viewBox="0 0 12 12"><path d="M2.5 1h2l1 3-1.3 1a6 6 0 0 0 2.8 2.8L8 6.5l3 1v2a1.5 1.5 0 0 1-1.5 1.5A8.5 8.5 0 0 1 1 2.5 1.5 1.5 0 0 1 2.5 1z" fill="#fff"/></svg></span>
          +64 21 473 5162
        </li>
        <li class="contact-item">
          <span class="contact-icon"><svg viewBox="0 0 12 12"><rect x="1" y="2.5" width="10" height="7" fill="none" stroke="#fff" stroke-width="1.2"/><path d="M1 2.5l5 4 5-4" fill="none" stroke="#fff" stroke-width="1.2"/></svg></span>
          danielf@harwickpartners.co.nz
        </li>
        <li class="contact-item">
          <span class="contact-icon"><svg viewBox="0 0 12 12"><circle cx="6" cy="6" r="4.8" fill="none" stroke="#fff" stroke-width="1.1"/><ellipse cx="6" cy="6" rx="2" ry="4.8" fill="none" stroke="#fff" stroke-width="1"/><path d="M1.2 6h9.6" stroke="#fff" stroke-width="1"/></svg></span>
          www.harwickpartners.co.nz
        </li>
      </ul>
    </div>
  </section>

  <section class="card card--back">
    <div class="brand">
      <span class="brand-mark"></span>
      <span class="brand-name">Harwick Partners</span>
    </div>
  </section>
</body>
</html>
```